Corvel Capital LLC

Need Professional Business cards for New Investment Fund

Target Market(s)

High Quality investors

Industry/Entity Type

Financial

Contact Information for Business Card

Phone Number +1 555 284 6190
Name Lukas Varenko
Title Fund Manager
email lv@FundCorvel.com
Website www.FundCorvel.com

Colors

Designer to choose colors to be used in the design.

Requirements
Must have
• Must have our Logo and all of the above. Must be made so lettering and loge can be raised

```html
<!DOCTYPE html>
<html lang="en">
<head>
<meta charset="utf-8">
<title>Fund Manager – Business Card</title>
<link href="https://fonts.googleapis.com/css2?family=Jost:wght@400;500;600;700&display=swap" rel="stylesheet">
<style>
  :root {
    --page: #e6e6e6;
    --card-white: #ffffff;
    --brand-green: #22ec00;
    --ink-dark: #464c44;
    --ink-text: #4a4f48;
  }
  html, body {
    margin: 0;
    padding: 0;
    width: 1200px;
    height: 1200px;
    overflow: hidden;
    background: var(--page);
    font-family: "Jost", sans-serif;
  }
  .sheet {
    width: 1200px;
    height: 1200px;
    display: flex;
    flex-direction: column;
    align-items: center;
    justify-content: center;
    gap: 90px;
  }
  .card {
    display: block;
    width: 880px;
    height: 503px;
  }
  .card-name { font-weight: 700; fill: var(--brand-green); font-size: 26px; letter-spacing: 0.3px; }
  .card-title { font-weight: 600; fill: var(--ink-dark); font-size: 18px; letter-spacing: 0.3px; }
  .card-contact { font-weight: 400; fill: var(--ink-text); font-size: 18px; letter-spacing: 0.4px; }
  .card-web { font-weight: 500; fill: #ffffff; font-size: 16px; letter-spacing: 3.6px; }
  .brand-name { font-weight: 600; fill: var(--ink-dark); letter-spacing: 1px; }
</style>
</head>
<body>
<main class="sheet">

  <svg class="card card-front" viewBox="0 0 800 457" aria-label="Business card front">
    <rect width="800" height="457" fill="var(--card-white)"/>

    <g class="brand">
      <rect x="584" y="150" width="30" height="30" fill="var(--brand-green)"/>
      <text class="brand-name" x="624" y="178" font-size="38">VARQEN</text>
    </g>

    <text class="card-name" x="41" y="304">Lukas Varenko</text>
    <text class="card-title" x="41" y="329">Fund Manager</text>

    <g class="contact-phone">
      <path d="M45 357 c0 0 2-2 3-1 l2 3 c0.5 1-1 2-1 2 c1 2 2 3 4 4 c0 0 1-1.5 2-1 l3 2 c1 1-1 3-1 3 c-6 1-13-6-12-12z" fill="var(--brand-green)"/>
      <text class="card-contact" x="68" y="371">+1 555 284 6190</text>
    </g>

    <g class="contact-email">
      <rect x="43" y="387" width="13" height="9" fill="var(--brand-green)"/>
      <path d="M43 387 l6.5 5 l6.5 -5" fill="none" stroke="#ffffff" stroke-width="1.2"/>
      <text class="card-contact" x="68" y="394">lv@FundCorvel.com</text>
    </g>

    <polygon points="0,418 350,418 392,457 0,457" fill="var(--ink-dark)"/>
    <polygon points="384,443 726,443 726,424 790,457 392,457" fill="var(--brand-green)"/>
    <text class="card-web" x="43" y="446">www.FundCorvel.com</text>
  </svg>

  <svg class="card card-back" viewBox="0 0 800 457" aria-label="Business card back">
    <rect width="800" height="457" fill="var(--brand-green)"/>
    <g class="brand">
      <rect x="262" y="208" width="40" height="40" fill="var(--ink-dark)"/>
      <text class="brand-name" x="316" y="245" font-size="52">VARQEN</text>
    </g>
  </svg>

</main>
</body>
</html>
```